Web Design for Webdesign company 3 page PSD

Project
---------
We need a PSD Web Design to be used in a WordPress installation.
What we would like to create is a professional looking website for a web design agency. We also need you to look for suitable stock images to be placed on these pages.
We need the design for:
Homepage
Landing page
Contact page
attached in the pages file you will find a file with more in depth details how these files should be build up.
We would like to see a desktop version and a mobile version of these pages
The website should have a 1100px width.
The mobile design should have 480px width.
The homepage should have a header slider about 450px high.
The slider is preferred full width and should have some images text and a button
Objectives
-------------
The main objective for the website is to get leads from customers in the form of a request for a quotation or a call or mail me back action. The most important action for the homepage is to link and navigate to our landing pages.
What we want to tell our visitors (our main products)
-------------------------------------------------------------------
- A website with no big investment but a monthly rate
- A successful website with no worries (a complete website, seo, hosting and a service contract for future customization is included for a monthly rate)
Color Scheme
------------
Use branding colors. You can find them in the branding.pdf file.
Additional colors:
White: #ffffff
Black: #181818
Company info
--------------
We are a starting web design / marketing agency based in The Netherlands and looking for the design of our website. Our services are (custom) webdesign, website marketing or combinations of both. Our main customer group is small business owners.
We sell websites but give the option to buy it with a lease contract.
A second product is a default website with a complete service: SEO, hosting and a service contract for a monthly rate.
Content:
-----------
If not available place Lorem Ipsum text.
There will come about 400 words of text on the landing pages
Design Competition
--------------------------
Since this is a designing competition we would like to see your creativity.
What you can expect from us is a lot of feedback 7 days a week with short response time.
You can send us the first sketchy mock ups of the homepage and we will give feedback based on these design. But we like your feedback or comments as well
Read the pages file for more in depth details how the pages should be designed

Target Market(s)
Small business owners in The Netherlands
Industry/Entity Type
It Company
Number of Pages Required
3 page
Requirements
Must have
- Homepage:
- Header slider with images, some text and a link to a custom page
- The slider should have 3 designed slides
- Landings page:
- Sidebar
- Action button for a request for a quotation
- Action button for a call me back action
- Action button for an appointment
- Contact form:
- Address details
- Contact form
Nice to have
- Homepage:
- Full width slider
- Testimonial block
- Blog items
Should not have
- Flash
- A to crowded design

```html
<!DOCTYPE html>
<html lang="en">
<head>
<meta charset="utf-8">
<title>Rising Oak Web Services – Landing</title>
<link rel="stylesheet" href="https://fonts.googleapis.com/css2?family=Montserrat:wght@400;700&family=Open+Sans:wght@400;600;700&display=swap">
<style>
:root{
  --teal-dark:#1f5d6a;
  --teal:#2d7a8a;
  --teal-mid:#4b8794;
  --teal-soft:#6fa1aa;
  --teal-pale:#93b9bf;
  --teal-paler:#b4cfd2;
  --green:#4f9a74;
  --green-band:#5e9e7e;
  --orange:#f5a21f;
  --ink:#181818;
  --text:#555;
  --muted:#999;
  --line:#e2e2e2;
  --side:#ececec;
  --foot:#2b2b2b;
  --foot-bar:#1e1e1e;
  --white:#ffffff;
}
*{box-sizing:border-box;margin:0;padding:0}
html,body{width:1200px;height:3556px;overflow:hidden;background:var(--white)}
body{position:relative;font-family:"Open Sans",Arial,sans-serif;color:var(--text);font-size:13px;line-height:1.6}
.abs{position:absolute}
h1,h2,h3,.heading{font-family:"Montserrat",Arial,sans-serif;font-weight:700;color:var(--ink);text-transform:uppercase}

/* header */
.site-header{left:0;top:0;width:1200px;height:104px}
.brand{left:95px;top:28px;display:flex;align-items:center;gap:14px}
.brand-mark{width:44px;height:44px;border-radius:50%;background:var(--green)}
.brand-name{font-family:"Montserrat",sans-serif;font-weight:700;font-size:20px;line-height:1.1;color:var(--teal-dark);width:200px}
.main-nav{right:92px;top:38px;display:flex;gap:22px;align-items:center}
.main-nav a{font-family:"Montserrat",sans-serif;font-size:13px;font-weight:700;color:var(--ink);text-decoration:none;text-transform:uppercase;padding:6px 14px;border-radius:16px}
.main-nav a.active{background:var(--teal-dark);color:var(--white)}

.page-band{left:0;top:104px;width:1200px;height:96px;background:linear-gradient(90deg,#4d8f6e,#6aa987 60%,#4d8f6e)}
.page-band h1{position:absolute;left:95px;top:32px;font-size:26px;color:var(--white)}
.breadcrumb{left:95px;top:220px;font-size:12px;color:var(--muted)}

/* sidebar */
.quick-links{left:95px;top:272px;width:219px;list-style:none}
.quick-links li{height:36px;margin-bottom:2px;background:var(--side);padding:0 14px;display:flex;justify-content:space-between;align-items:center;font-size:13px;color:#666}
.quick-links li::after{content:"›";font-size:18px;color:#999}
.quick-links li.active{background:var(--teal);color:var(--white)}
.quick-links li.active::after{color:var(--white)}
.quote-box{left:95px;top:678px;width:219px;height:344px;background:var(--side);padding:0 12px}
.quote-box h3{margin:0 -12px 12px;height:40px;background:var(--green-band);color:var(--white);font-size:15px;text-align:center;line-height:40px}
.field{background:var(--white);border:1px solid #ccc;height:30px;margin-bottom:13px;padding:0 8px;font-size:12px;line-height:28px;color:#777}
.field.tall{height:112px}
.btn-submit{display:block;background:var(--orange);color:var(--white);font-family:"Montserrat",sans-serif;font-weight:700;font-size:13px;text-align:center;height:32px;line-height:32px}

/* content */
.hero{left:344px;top:272px;width:764px;height:374px;background:linear-gradient(120deg,#0e3a45,#1f5d6a 55%,#3a8897);overflow:hidden}
.hero-kicker{position:absolute;left:30px;top:44px;font-family:"Montserrat",sans-serif;font-weight:700;color:var(--white);font-size:22px;line-height:1.2}
.hero-kicker strong{display:block;font-size:42px}
.hero-devices{position:absolute;left:60px;top:150px;width:440px;height:200px;background:linear-gradient(135deg,#e25a4e,#3fa9e0 45%,#f6c238 80%,#f08a24);border-radius:6px;opacity:.9}
.hero-side{position:absolute;left:520px;top:170px;font-family:"Montserrat",sans-serif;font-weight:700;color:var(--white);font-size:16px;line-height:1.3;text-transform:uppercase}

.section-title{font-size:20px}
.intro{left:344px;top:668px;width:764px}
.intro p{margin-top:14px}
.brands-title{left:344px;top:886px;width:764px;text-align:center;font-size:22px}
.diagram{left:344px;top:920px;overflow:visible}
.success-visual{left:637px;top:1517px;width:281px;height:187px;background:linear-gradient(135deg,#e25a4e,#3fa9e0 50%,#f6c238);border-radius:6px}

.feature h2{font-size:22px;margin-bottom:14px}
.feature p{margin-bottom:14px}
.photo{border-radius:2px}
.feat-1{left:344px;top:1780px;width:338px}
.photo-1{left:711px;top:1778px;width:391px;height:340px;background:linear-gradient(135deg,#d7e3ea,#8fb3c6 50%,#e8d7a8)}
.photo-2{left:344px;top:2207px;width:338px;height:341px;background:radial-gradient(circle at 50% 45%,#eef3f6,#c5d6e0 70%,#a8bfcc)}
.feat-2{left:776px;top:2205px;width:332px}
.feat-3{left:344px;top:2632px;width:338px}
.photo-3{left:711px;top:2607px;width:391px;height:386px;background:linear-gradient(180deg,#f4f4f4,#6b7280 40%,#23272d 80%,#f4f4f4)}

.cta{top:3061px;width:243px;height:65px;display:flex;align-items:center;gap:16px;padding-left:22px;color:var(--white);font-family:"Montserrat",sans-serif;font-weight:700;font-size:16px;line-height:1.1;text-transform:uppercase}
.cta-icon{width:40px;height:40px;border-radius:50%;border:2px solid var(--white);flex:none;display:flex;align-items:center;justify-content:center}
.cta-call{left:344px;background:var(--green-band)}
.cta-appt{left:604px;background:var(--orange)}
.cta-quote{left:865px;background:var(--teal)}

/* footer */
.site-footer{left:0;top:3170px;width:1200px;height:320px;background:var(--foot);color:#bbb;font-size:12px}
.foot-col{position:absolute;top:64px}
.foot-col h4{font-family:"Montserrat",sans-serif;font-weight:700;color:var(--white);font-size:14px;text-transform:uppercase;margin-bottom:14px;line-height:1.2}
.foot-col ul{list-style:none}
.foot-col li{line-height:22px}
.foot-input{width:240px;height:30px;background:var(--white);color:#888;padding:0 10px;line-height:30px;margin-bottom:10px}
.foot-btn{width:240px;height:30px;background:var(--green-band);color:var(--white);font-family:"Montserrat",sans-serif;font-weight:700;text-align:center;line-height:30px}
.contact-row{display:flex;gap:10px;margin-bottom:10px;line-height:1.5}
.social-row{display:flex;align-items:center;gap:10px;margin-bottom:12px}
.social-dot{width:26px;height:26px;border-radius:50%;border:1px solid #aaa;flex:none}
.foot-bar{left:0;top:3490px;width:1200px;height:66px;background:var(--foot-bar);color:#aaa;font-size:12px;text-align:center;padding-top:12px;line-height:22px}
</style>
</head>
<body>

<header class="site-header abs">
  <div class="brand abs"><span class="brand-mark"></span><span class="brand-name">RISING OAK WEB SERVICES</span></div>
  <nav class="main-nav abs">
    <a href="#">Home</a><a href="#" class="active">Landing</a><a href="#">Testimonials</a><a href="#">Blog</a><a href="#">Contact</a>
  </nav>
</header>

<div class="page-band abs"><h1>Landing</h1></div>
<div class="breadcrumb abs">Home &nbsp;›&nbsp; Landing</div>

<aside>
  <ul class="quick-links abs">
    <li>Quick Link 01</li><li class="active">Quick Link 02</li><li>Quick Link 03</li><li>Quick Link 04</li><li>Quick Link 05</li>
    <li>Quick Link 06</li><li>Quick Link 07</li><li>Quick Link 08</li><li>Quick Link 09</li><li>Quick Link 10</li>
  </ul>
  <div class="quote-box abs">
    <h3>Request a Quote</h3>
    <div class="field">Name</div>
    <div class="field">Email</div>
    <div class="field">Phone</div>
    <div class="field tall">Message</div>
    <span class="btn-submit">SUBMIT</span>
  </div>
</aside>

<main>
  <section class="hero abs">
    <div class="hero-kicker">WE BUILD FULL<strong>SERVICE WEBSITE</strong></div>
    <div class="hero-devices" role="img" aria-label="Laptop, desktop monitor, tablet and phones showing a website"></div>
    <div class="hero-side">A full-service Rising Oak<br>approach to grow<br>your brand online</div>
  </section>

  <section class="intro abs">
    <h2 class="section-title">We make you look good online</h2>
    <p>Lorem ipsum dolor sit amet, cu per augue graeco cotidieque. Est ut novum laudem definiebas, no augue necessitatibus nam. Te errem dissentias appellantur cum, errem menttum conceptam ad eum. Ad has melius adipisci, eu sed iracundia repririque, elus perpetua vis te. Fuisset democritum scribentur ex est, mei ei viderer sapientem suscipiantur.</p>
    <p>Euismod appareat explicari et quo. Mei in natum errem scribentur, idque affert abhorreant ei pri, ex eum torquatos adolescens. Errorbus conclusionemque cu quo. Novum putent his eu.</p>
  </section>

  <h2 class="brands-title abs">We build brands</h2>

  <svg class="diagram abs" width="764" height="800" viewBox="0 0 764 800" aria-label="Process diagram from company name to success">
    <defs>
      <marker id="arrow" viewBox="0 0 10 10" refX="8" refY="5" markerWidth="7" markerHeight="7" orient="auto"><path d="M0 0L10 5L0 10z" fill="#9aa"/></marker>
    </defs>
    <g fill="none" stroke="#aab" stroke-width="2" marker-end="url(#arrow)">
      <path d="M262 95 Q282 70 300 100"/>
      <path d="M516 95 Q548 70 583 100"/>
      <path d="M410 238 L410 258"/>
      <path d="M348 320 Q230 320 205 412"/>
      <path d="M472 320 Q545 320 560 412"/>
      <path d="M290 493 L474 493"/>
      <path d="M201 573 Q205 625 285 640"/>
      <path d="M563 575 Q570 625 582 640"/>
    </g>
    <g font-family="Montserrat, Arial, sans-serif" font-weight="700" font-size="15" fill="#fff" text-anchor="middle">
      <circle cx="157" cy="126" r="105" fill="#1f5d6a"/>
      <text x="157" y="122">COMPANY</text><text x="157" y="141">NAME</text>
      <circle cx="410" cy="126" r="105" fill="#4b8794"/>
      <text x="410" y="132">LOGO</text>
      <circle cx="688" cy="126" r="105" fill="#6fa1aa"/>
      <text x="688" y="132">DESIGN</text>
      <circle cx="410" cy="325" r="62" fill="#6fa1aa"/>
      <text x="410" y="320" font-size="13">WEBSITE</text><text x="410" y="338" font-size="13">CONTENT</text>
      <circle cx="201" cy="493" r="78" fill="#93b9bf"/>
      <text x="201" y="499">SEO</text>
      <circle cx="563" cy="493" r="78" fill="#b4cfd2"/>
      <text x="563" y="499">SALES</text>
    </g>
  </svg>
  <div class="success-visual abs" role="img" aria-label="Devices displaying the word success"></div>

  <section class="feature feat-1 abs">
    <h2>A successful website</h2>
    <p>Lorem ipsum dolor sit amet, cu per augue graeco cotidieque. Est ut novum laudem definiebas, no augue necessitatibus nam. Te errem dissentias appellantur cum, errem menttum conceptam ad eum. Ad has melius adipisci, eu sed iracundia repririque, elus perpetua vis te. Fuisset democritum scribentur ex est, mei ei viderer sapientem suscipiantur.</p>
    <p>Euismod appareat explicari et quo. Mei in natum errem scribentur, idque affert abhorreant ei pri, ex eum torquatos adolescens. Errorbus conclusionemque cu quo. Novum putent his eu.</p>
  </section>
  <div class="photo photo-1 abs" role="img" aria-label="Man with a laptop surrounded by floating website screens"></div>

  <div class="photo photo-2 abs" role="img" aria-label="Hand touching an SEO process diagram with keywords"></div>
  <section class="feature feat-2 abs">
    <h2>SEO optimized with a service contract</h2>
    <p>Lorem ipsum dolor sit amet, cu per augue graeco cotidieque. Est ut novum laudem definiebas, no augue necessitatibus nam. Te errem dissentias appellantur cum, errem menttum conceptam ad eum. Ad has melius adipisci, eu sed iracundia repririque, elus perpetua vis te. Fuisset democritum scribentur ex est, mei ei viderer sapientem suscipiantur.</p>
    <p>Euismod appareat explicari et quo. Mei in natum errem scribentur, idque affert abhorreant ei pri, ex eum torquatos adolescens. Errorbus conclusionemque cu quo. Novum putent his eu.</p>
  </section>

  <section class="feature feat-3 abs">
    <h2>Hosting service</h2>
    <p>Lorem ipsum dolor sit amet, cu per augue graeco cotidieque. Est ut novum laudem definiebas, no augue necessitatibus nam. Te errem dissentias appellantur cum, errem menttum conceptam ad eum. Ad has melius adipisci, eu sed iracundia repririque, elus perpetua vis te. Fuisset democritum scribentur ex est, mei ei viderer sapientem suscipiantur.</p>
    <p>Euismod appareat explicari et quo. Mei in natum errem scribentur, idque affert abhorreant ei pri, ex eum torquatos adolescens. Errorbus conclusionemque cu quo. Novum putent his eu.</p>
  </section>
  <div class="photo photo-3 abs" role="img" aria-label="Row of server racks in a data centre"></div>

  <a class="cta cta-call abs"><span class="cta-icon"><svg width="20" height="20" viewBox="0 0 24 24"><path d="M6.6 10.8a15 15 0 0 0 6.6 6.6l2.2-2.2c.3-.3.7-.4 1-.2 1.1.4 2.3.6 3.6.6.6 0 1 .4 1 1V20c0 .6-.4 1-1 1A17 17 0 0 1 3 4c0-.6.4-1 1-1h3.5c.6 0 1 .4 1 1 0 1.2.2 2.4.6 3.6.1.3 0 .7-.2 1z" fill="#fff"/></svg></span>Call me<br>back</a>
  <a class="cta cta-appt abs"><span class="cta-icon"><svg width="20" height="20" viewBox="0 0 24 24" fill="none" stroke="#fff" stroke-width="2"><rect x="3" y="5" width="18" height="16"/><path d="M3 10h18M8 3v4M16 3v4"/></svg></span>Make an<br>appointment</a>
  <a class="cta cta-quote abs"><span class="cta-icon"><svg width="20" height="20" viewBox="0 0 24 24" fill="none" stroke="#fff" stroke-width="2"><path d="M6 3h9l4 4v14H6z M9 12h7M9 16h7"/></svg></span>Request a<br>quotation</a>
</main>

<footer class="site-footer abs">
  <div class="foot-col" style="left:95px">
    <h4>Subscribe to<br>our newsletter</h4>
    <div class="foot-input">Enter Your Name</div>
    <div class="foot-input">Enter Your Email</div>
    <div class="foot-btn">SUBSCRIBE</div>
  </div>
  <div class="foot-col" style="left:403px">
    <h4>Quick Links</h4>
    <ul><li>Home</li><li>Landing</li><li>Testimonials</li><li>Blog</li><li>Contact</li></ul>
  </div>
  <div class="foot-col" style="left:607px">
    <h4>Contact Info</h4>
    <div class="contact-row"><svg width="14" height="16" viewBox="0 0 24 24"><path d="M12 2a7 7 0 0 0-7 7c0 5 7 13 7 13s7-8 7-13a7 7 0 0 0-7-7zm0 9.5a2.5 2.5 0 1 1 0-5 2.5 2.5 0 0 1 0 5z" fill="#bbb"/></svg><span>12 Oak Lane, Suite 4<br>Greenfield, 1000 AB</span></div>
    <div class="contact-row"><svg width="14" height="16" viewBox="0 0 24 24"><path d="M6.6 10.8a15 15 0 0 0 6.6 6.6l2.2-2.2c.3-.3.7-.4 1-.2 1.1.4 2.3.6 3.6.6.6 0 1 .4 1 1V20c0 .6-.4 1-1 1A17 17 0 0 1 3 4c0-.6.4-1 1-1h3.5c.6 0 1 .4 1 1 0 1.2.2 2.4.6 3.6.1.3 0 .7-.2 1z" fill="#bbb"/></svg><span>Phone: (000) 555-0142<br>Fax: (000) 555-0143</span></div>
    <div class="contact-row"><svg width="14" height="16" viewBox="0 0 24 24" fill="none" stroke="#bbb" stroke-width="2"><rect x="3" y="5" width="18" height="14"/><path d="M3 6l9 7 9-7"/></svg><span>Email: hello@risingoakweb.example<br>Website: www.risingoakweb.example</span></div>
  </div>
  <div class="foot-col" style="left:883px">
    <h4>Stay Connected</h4>
    <div class="social-row"><span class="social-dot"></span>Follow Us On Friendspace</div>
    <div class="social-row"><span class="social-dot"></span>Follow Us On Chirpline</div>
    <div class="social-row"><span class="social-dot"></span>Follow Us On ProNetwork</div>
  </div>
</footer>
<div class="foot-bar abs">© 2015 Rising Oak All Rights Reserved.<br>Terms of Use &nbsp;|&nbsp; Legal Disclaimer &nbsp;|&nbsp; Privacy Policy &nbsp;|&nbsp; References</div>

</body>
</html>
```